Veterinary Pylon

My veterinary clinic is not clearly visible from the street and I want to place a Pylon next to my driveway. I want a modern, elegant straight Design, the Photo shows the sheduled place. One can see the clinic on our Homepage: www.tailbright-vethaus.at
The last pictures are examples for pylones I like

Target Market(s)

the passing cars often miss my entry...I want to show where to turn left

Colors
3276b5
33a6d7
00a990

Requirements
Must have
• High value, simple elegance, size: 250cm (high) x 100cm (width)
Nice to have
• Our Logo, arrow(?)

A special Text is not necessary but this will be an option:

Biegen sie hier ab und wir biegen es wieder hin!
Should not have
• Too much Color, the colors I have chosen are the possible colors but it‘s not necessary to use them.

```html
<!DOCTYPE html>
<html lang="de">
<head>
<meta charset="utf-8">
<title>Tailbright Vethaus – Pylon</title>
<link rel="stylesheet" href="https://fonts.googleapis.com/css2?family=Archivo+Black&display=swap">
<style>
  :root {
    --navy: #134b93;
    --sky: #2eb9dc;
    --mist: #e6edf6;
    --paper: #ffffff;
  }
  html, body {
    margin: 0;
    padding: 0;
    width: 1200px;
    height: 3000px;
    overflow: hidden;
    background: var(--paper);
  }
  .pylon {
    position: relative;
    width: 1200px;
    height: 3000px;
    background: var(--paper);
    overflow: hidden;
  }
  .top-swoosh {
    position: absolute;
    top: 0;
    left: 0;
    width: 1200px;
    height: 340px;
  }
  .brand-dot {
    position: absolute;
    top: 470px;
    left: 0;
    width: 1200px;
    height: 510px;
  }
  .clinic-name,
  .faint-name {
    position: absolute;
    left: 0;
    width: 1200px;
    margin: 0;
    font-family: "Archivo Black", sans-serif;
    font-weight: 400;
  }
  .clinic-name { top: 1100px; height: 400px; }
  .clinic-name text { fill: var(--navy); }
  .faint-name { top: 2320px; height: 680px; }
  .faint-name text { fill: var(--mist); }
  .turn-arrow {
    position: absolute;
    top: 1604px;
    left: 368px;
    width: 488px;
    height: 488px;
  }
</style>
</head>
<body>
  <main class="pylon">
    <svg class="top-swoosh" viewBox="0 0 1200 340" aria-hidden="true">
      <path d="M0 0 H1138 C960 190 700 360 300 318 C230 312 160 300 95 283 C300 320 560 300 760 220 C880 170 990 90 1070 0 Z" fill="var(--sky)"/>
      <path d="M0 0 H1032 C850 170 560 300 280 278 C180 272 80 260 0 245 Z" fill="var(--navy)"/>
    </svg>

    <svg class="brand-dot" viewBox="0 0 1200 510" aria-hidden="true">
      <circle cx="612" cy="255" r="240" fill="var(--sky)"/>
    </svg>

    <svg class="clinic-name" viewBox="0 0 1200 400" role="img" aria-label="Tailbright Vethaus">
      <text x="152" y="175" font-size="200" textLength="920" lengthAdjust="spacingAndGlyphs">TAILBRIGHT</text>
      <text x="152" y="375" font-size="170" textLength="920" lengthAdjust="spacingAndGlyphs">VETHAUS</text>
    </svg>

    <svg class="turn-arrow" viewBox="0 0 486 486" role="img" aria-label="Hier links abbiegen">
      <defs>
        <linearGradient id="arrowFill" x1="0" y1="0" x2="1" y2="0">
          <stop offset="0" stop-color="#134b93"/>
          <stop offset="1" stop-color="#2eb9dc"/>
        </linearGradient>
      </defs>
      <circle cx="243" cy="243" r="243" fill="url(#arrowFill)"/>
      <g fill="none" stroke="#ffffff" stroke-width="23">
        <line x1="115" y1="243" x2="387" y2="243"/>
        <polyline points="218,132 107,243 218,354"/>
      </g>
    </svg>

    <svg class="faint-name" viewBox="0 0 1200 680" aria-hidden="true">
      <text x="115" y="250" font-size="260" textLength="990" lengthAdjust="spacingAndGlyphs">TAILBRIGHT</text>
      <text x="115" y="560" font-size="300" textLength="990" lengthAdjust="spacingAndGlyphs">VETHAUS</text>
    </svg>
  </main>
</body>
</html>
```